Brochure Design Project - Glass Cabinets

We are a small but rapidly expanding company providing glass display furniture to retailers and other organisations to display their product. We specialise in all-glass, frameless display cabinets and showcases. Our products include glass cabinets, wall units, shelving units, etc. Our main market was initially householders, then retailers, but has increasingly become corporates who want to display their corporate prizes/trophies, and are also fit-out companies who have discovered our products and are interested in them. We want to make the most of this development, and we want this brochure to help us.
We have identified shop fit-out companies and fit-out designers as a target market for the coming year, so we need some literature that will introduce our company to these businesses, and encourage them to use our products in their designs.
This brochure will not be a product catalogue (we already have that), but a corporate profile that introduces our company and its services. We need to communicate the message that we are a serious provider of good quality glass display furniture, and that we stand for innovation, value, and good design.
We will be giving these brochures out when we make marketing approaches to the shop fit-out companies.
We envisage that the brochure will be a one A4 page brochure, with the back side used for examples of our work. We are open to suggestions about this, however. For example, it could conceivably be DLE format.
We expect some of the copy will be in text boxes. We will upload further details of the examples on page 2 in the next few days.
It needs to be full colour.
It will be offset printed.
The output needs to be PC compatible, preferably produced in Indesign so it is compatible with our software.
Please see our website and other uploaded files for examples of our current imagery. The corporate brochure needn't follow this slavishly, but should be cognizant of it.

Reason: The deadline has been extended because there is some further information I will put up, regarding page two. Also, I will spend some time providing feedback.

Thank you to all who have submitted designs for my project. They are all very much appreciated. I have responded to most of you, but some general comments that come to mind are that the brochure needs to 1) appeal to the emotions more i.e. be more evocative of sophistication. This means not necessarily using just the images I have uploaded, but maybe suggest design elements that are more creative than 'blocky', and 2) be designed to sell the company rather than its products. This is partly my fault, I think, although it is a learning experience for me also. In general I think there is too much information to include, especially copy but also images, forcing designers to make the designs quite boring in order to accommodate it. I intend to cut the information significantly and will repost. Having said that, I am trying to see through the overload of information and look for designs that include elements that are creative and sophisticated. Sometimes less is more. Apologies if I am confusing you, but the main thing is to make the brochure appeal to the emotions i.e. 'this company is sophisticated and and be depended upon', and less to the products themselves. I welcome any questions you may have.

Thanks to all the designers who have submitted designs. There are some great ideas coming through now, and on the basis of these ideas I have been able to determine what the brochure needs to look like much more precisely. Some of the designs have been too crowded, because there has been too much information to include. I have therefore decided that the brochure needs to be a 4 page A4 brochure (A3 folded in half). I have altered the copy in the Word document to reflect this. The middle spread is now dedicated to jobs previously done, and includes logos of other high profile customers. The front page can now be dedicated to providing very basic, introductory information and an eye-catching graphic, while the back page has further detail about the company and contact details. To reflect the fact that this will involve some redesign work, I have increased the budget. I have also extended the deadline by a week. I thank you for your patience, but sometimes a design project is iterative. Please see the newly uploaded files.

Reason: Thanks to all the designers who have submitted designs. There are some great ideas coming through now, and on the basis of these ideas I have been able to determine what the brochure needs to look like much more precisely. Some of the designs have been too crowded, because there has been too much information to include. I have therefore decided that the brochure needs to be a 4 page A4 brochure (A3 folded in half). I have altered the copy in the Word document to reflect this. The middle spread is now dedicated to jobs previously done, and includes logos of other high profile customers. The front page can now be dedicated to providing very basic, introductory information and an eye-catching graphic, while the back page has further detail about the company and contact details. To reflect the fact that this will involve some redesign work, I have increased the budget. I have also extended the deadline by a week. I thank you for your patience, but sometimes a design project is iterative. Please see the newly uploaded files.

Target Market(s)

Shop Fit-out companies, Fit-out designers, Retailers

Industry/Entity Type

Marketing

Requirements
Must have
• Existing logo
Full colour, with overprint

```html
<!DOCTYPE html>
<html lang="en">
<head>
<meta charset="utf-8">
<title>Vitrine Lane – Brochure Cover</title>
<link rel="stylesheet" href="https://fonts.googleapis.com/css2?family=Source+Sans+3:wght@300;400;600;700&display=swap">
<style>
  :root {
    --backdrop: #2b2b2b;
    --brand-green: #8cb43c;
    --brand-green-dark: #7aa22f;
    --white: #ffffff;
    --ink-grey: #555555;
    --headline-ink: #1c1c1a;
    --panel-top: #f2f2f2;
    --panel-bottom: #c6c6c6;
    --divider: #a9a9a9;
    --photo-dark: #141514;
    --photo-mid: #4b4d49;
    --photo-light: #e2dfcc;
  }
  * { box-sizing: border-box; margin: 0; padding: 0; }
  html, body {
    width: 1200px; height: 793px; overflow: hidden;
    background: var(--backdrop);
    font-family: "Source Sans 3", Arial, sans-serif;
  }
  .brochure {
    position: absolute; left: 350px; top: 43px;
    width: 500px; height: 706px;
    background: var(--white);
    overflow: hidden;
  }

  /* Masthead */
  .masthead {
    position: absolute; left: 0; top: 0; width: 500px; height: 152px;
    background: var(--brand-green);
  }
  .brand-mark {
    position: absolute; left: 76px; top: 60px;
    width: 54px; height: 54px;
    background: rgba(255,255,255,0.55);
  }
  .brand-name {
    position: absolute; left: 141px; top: 55px;
    color: var(--white); font-size: 37px; font-weight: 600;
    letter-spacing: 0.5px; line-height: 1;
  }
  .tagline {
    position: absolute; left: 141px; top: 92px;
    color: var(--white); font-size: 22px; font-weight: 400; line-height: 1;
  }

  /* Hero */
  .hero {
    position: absolute; left: 0; top: 152px; width: 500px; height: 368px;
  }
  .hero-photo {
    position: absolute; inset: 0;
    background:
      radial-gradient(ellipse 135px 115px at 360px 190px, var(--photo-light) 0%, rgba(150,148,130,0.7) 50%, rgba(0,0,0,0) 100%),
      radial-gradient(ellipse 280px 220px at 240px 110px, var(--photo-mid) 0%, var(--photo-dark) 100%);
  }
  .intro {
    position: absolute; left: 34px; top: 144px; width: 116px;
    color: var(--white); font-size: 10.4px; line-height: 12.2px;
    hyphens: auto;
  }
  .intro p + p { margin-top: 12px; }
  .intro strong { font-weight: 700; }
  .values-headline {
    position: absolute; left: 286px; top: 137px;
    color: var(--headline-ink); font-size: 26px; font-weight: 300; line-height: 30px;
  }

  /* Feature panel */
  .features {
    position: absolute; left: 0; top: 520px; width: 500px; height: 156px;
    background: linear-gradient(var(--panel-top), var(--panel-bottom));
    border-top: 3px solid var(--white);
  }
  .feature-panel {
    position: absolute; left: 25px; top: 20px; width: 446px; height: 110px;
    border: 1px solid rgba(255,255,255,0.9); border-radius: 14px;
    background: linear-gradient(rgba(255,255,255,0.55), rgba(255,255,255,0.15));
    display: flex; padding: 9px 0 8px 16px;
  }
  .feature { padding-right: 5px; }
  .feature + .feature { border-left: 1px solid var(--divider); padding-left: 6px; }
  .feature:nth-child(1) { width: 103px; }
  .feature:nth-child(2) { width: 105px; }
  .feature:nth-child(3) { width: 105px; }
  .feature:nth-child(4) { width: 110px; }
  .feature h3 {
    color: var(--brand-green-dark); font-size: 13px; font-weight: 700;
    line-height: 14px;
  }
  .feature p { color: var(--ink-grey); font-size: 7px; line-height: 9.4px; hyphens: auto; }

  /* Footer */
  .footer-band {
    position: absolute; left: 0; top: 676px; width: 500px; height: 30px;
    background: var(--brand-green);
    color: var(--white); font-size: 9.5px; font-weight: 700;
    text-align: center; line-height: 30px;
  }
</style>
</head>
<body>
  <main class="brochure">
    <header class="masthead">
      <span class="brand-mark"></span>
      <div class="brand-name">VITRINE LANE</div>
      <div class="tagline">clarity craft care</div>
    </header>

    <section class="hero">
      <div class="hero-photo" role="img" aria-label="Dimly lit modern gallery interior with an illuminated frameless glass display cabinet"></div>
      <div class="intro">
        <p><strong>Vitrine Lane</strong> is one of New Zealand's leading suppliers of high quality showcases, display cases and display cabinets.</p>
        <p><strong>We specialise</strong> in all-glass display cabinets that minimise visual obstructions to the cabinet's contents.</p>
        <p><strong>Our range is unique</strong>, our service is exceptional, our attention to detail will surprise you.</p>
      </div>
      <div class="values-headline">UNIQUE<br>INNOVATIVE<br>CREATIVE</div>
    </section>

    <section class="features">
      <div class="feature-panel">
        <div class="feature">
          <h3>SERVICE</h3>
          <p>We believe in providing customers with well-designed, high quality products at a great price. Our standard range is kept in stock, so we can supply immediately.</p>
        </div>
        <div class="feature">
          <h3>VALUE</h3>
          <p>All glass and components are of the highest quality.</p>
        </div>
        <div class="feature">
          <h3>RANGE</h3>
          <p>As well as New Zealand's largest range of frameless glass cabinets, we also stock a range of framed cabinets, counters, free-standing shelving units, wall units, and kiosk counters. Custom made cabinets can be a single unit to a shop lot.</p>
        </div>
        <div class="feature">
          <h3>STRENGTH</h3>
          <p>All glass is 6.1mm or 7.1mm toughened glass.</p>
        </div>
      </div>
    </section>

    <footer class="footer-band">www.vitrinelane.co.nz</footer>
  </main>
</body>
</html>
```